Post Card Design - Photo on front, details on back. Logo on both sides.

Back: See the photo of my old card. The back worked well, as it gave me lots of space to write on. The address details are still correct, but the logo has changed to Josephine Sans. Logo can be on one line or on two (if two, align it on the left).
Don't include the 'BEAUTIFUL WEDDING DRESSES...' bit.
I'd like to print this on thicker, slightly coarse paper, so don't go too small on detail.
Here are the Trelo paper details: Paper Stock: Natural Uncoated
Paper Thickness: Premium
Finish: None
Front of Card: I'd like to see options for both pictures:
I think the painted image would look best with a frame in a pale shade and the logo in the frame fairly subtle.
The actual dress photo I'd like to see cropped a bit like in my mock up. You'll need to have a look at how the logo would be best placed on this. You can place it anywhere, or add a banner.
See my website for my brand's look: mirelhoffkin.co.nz
Target Market(s)
Brides
Industry/Entity Type
Wedding Dresses
Contact Information for Business Card
Front: Photo and logo. Back: with details and lots of empty space. See attached photos for loose brief.
Other font styles liked:
- Josephine Sans
Requirements
Must have
- I hand-write the gown designs and price on the back of the card, so there needs to be plenty of empty space.
Nice to have
- As per brief.
Should not have
- It must look clean, romantic, modern. Timeless.

```html
<!DOCTYPE html>
<html lang="en">
<head>
<meta charset="utf-8">
<title>Mirel Hoffkin — Business Card</title>
<link href="https://fonts.googleapis.com/css2?family=Josefin+Sans:wght@200;300&family=Open+Sans:wght@400&display=swap" rel="stylesheet">
<style>
  :root {
    --backdrop: #ecedf0;
    --card-white: #ffffff;
    --ink: #1a1a1a;
    --logo-white: #ffffff;
    --edge-gold: #a8802a;
    --photo-light: #eedfca;
    --photo-mid: #d9bd98;
    --photo-deep: #b48b62;
  }
  * { box-sizing: border-box; margin: 0; padding: 0; }
  html, body {
    width: 1200px;
    height: 1200px;
    overflow: hidden;
    background: var(--backdrop);
  }
  .canvas {
    position: relative;
    width: 1200px;
    height: 1200px;
  }
  .card {
    position: absolute;
    left: 170px;
    width: 860px;
    height: 500px;
    border-bottom: 5px solid var(--edge-gold);
    box-shadow: 0 6px 18px rgba(0, 0, 0, 0.12);
    overflow: hidden;
  }
  .card--front { top: 70px; }
  .card--back {
    top: 620px;
    background: var(--card-white);
  }
  .front__photo {
    position: absolute;
    inset: 0;
    background:
      radial-gradient(ellipse at 70% 45%, rgba(255, 245, 230, 0.7), transparent 60%),
      linear-gradient(120deg, var(--photo-deep) 0%, var(--photo-mid) 35%, var(--photo-light) 70%, var(--photo-mid) 100%);
  }
  .front__logo {
    position: absolute;
    top: 26px;
    left: 70px;
    writing-mode: vertical-rl;
    color: var(--logo-white);
    font-family: "Josefin Sans", sans-serif;
    text-transform: uppercase;
    line-height: 1;
  }
  .front__logo-first {
    display: block;
    font-size: 118px;
    font-weight: 200;
    letter-spacing: 8px;
  }
  .front__logo-last {
    display: block;
    font-size: 58px;
    font-weight: 200;
    letter-spacing: 5px;
    margin-right: 6px;
  }
  .back__name {
    position: absolute;
    top: 48px;
    left: 54px;
    font-family: "Josefin Sans", sans-serif;
    font-weight: 300;
    font-size: 36px;
    letter-spacing: 3px;
    color: var(--ink);
    text-transform: uppercase;
  }
  .back__contacts {
    position: absolute;
    right: 54px;
    bottom: 40px;
    list-style: none;
    font-family: "Open Sans", sans-serif;
    font-size: 27px;
    color: var(--ink);
  }
  .contact {
    display: flex;
    align-items: center;
    gap: 12px;
    line-height: 1.45;
  }
  .contact__icon {
    width: 20px;
    height: 20px;
    flex: none;
    fill: none;
    stroke: var(--ink);
    stroke-width: 1.6;
  }
  .contact__icon--solid { fill: var(--ink); stroke: none; }
</style>
</head>
<body>
<main class="canvas">
  <section class="card card--front">
    <div class="front__photo" role="img" aria-label="Photograph of a bride in a flowing ivory gown in a warm, sunlit stone room"></div>
    <h1 class="front__logo">
      <span class="front__logo-first">Mirel</span>
      <span class="front__logo-last">Hoffkin</span>
    </h1>
  </section>

  <section class="card card--back">
    <h2 class="back__name">Mirel Hoffkin</h2>
    <ul class="back__contacts">
      <li class="contact">
        <svg class="contact__icon contact__icon--solid" viewBox="0 0 20 20" aria-hidden="true">
          <path d="M6 2 L8.5 2 L9.5 6 L7.6 7.4 C8.4 9.6 10.2 11.5 12.5 12.4 L13.9 10.5 L18 11.5 L18 14 C18 16 16.5 17.5 14.5 17.2 C8 16.2 3.8 12 2.8 5.5 C2.5 3.5 4 2 6 2 Z"/>
        </svg>
        <span>1+64 9 412 5637</span>
      </li>
      <li class="contact">
        <svg class="contact__icon" viewBox="0 0 20 20" aria-hidden="true">
          <circle cx="10" cy="10" r="8"/>
          <ellipse cx="10" cy="10" rx="3.5" ry="8"/>
          <line x1="2" y1="10" x2="18" y2="10"/>
          <line x1="3.2" y1="6" x2="16.8" y2="6"/>
          <line x1="3.2" y1="14" x2="16.8" y2="14"/>
        </svg>
        <span>mirelhoffkin.co.nz</span>
      </li>
      <li class="contact">
        <svg class="contact__icon" viewBox="0 0 20 20" aria-hidden="true">
          <rect x="2" y="4.5" width="16" height="11"/>
          <polyline points="2,4.5 10,11 18,4.5"/>
        </svg>
        <span>mira@mirelhoffkin.co.nz</span>
      </li>
    </ul>
  </section>
</main>
</body>
</html>
```